Redesign website for small print company

Vindurgata is a small printing company in Iceland mainly servicing Students, schools, etc. We are also doing all kind of other jobs, like business cards, book printing, brochure printing etc. We are also selling books online.
Our website is: www.vindurgata.is
What we are looking for is:
- Web Design (Uncoded - PSD layout only)
- Mobile friendly design, using our current color scheme: Red, green, yellow and light gray.
- Clean simple design
- Simple, light and easy to use.
- More menu Items/drop down
Industry/Entity Type
Digital Printing
Number of Pages Required
5+ page
Requirements
Must have
- Easy navigation
- Designed for mobile
- Current color scheme (see logo)
Nice to have
- Icon based products

```html
<!DOCTYPE html>
<html lang="en">
<head>
<meta charset="utf-8">
<title>Vindurgata – Printing Services</title>
<link href="https://fonts.googleapis.com/css2?family=Poppins:wght@400;500;600;700&display=swap" rel="stylesheet">
<style>
:root{
  --red:#e8402f;
  --green:#1e6b3c;
  --yellow:#f6c817;
  --light:#f2f2f2;
  --card:#ebedf0;
  --dark:#262626;
  --text:#333;
  --muted:#555;
}
*{box-sizing:border-box;margin:0;padding:0}
html,body{width:1200px;height:3536px;overflow:hidden;background:#fff}
body{font-family:'Poppins',sans-serif;color:var(--text);position:relative}
.abs{position:absolute}

/* header */
.site-header{position:absolute;top:0;left:0;width:1200px;height:113px;background:#fff}
.brand{position:absolute;left:96px;top:28px;display:flex;align-items:center;gap:14px}
.brand-mark{width:46px;height:46px;background:var(--red)}
.brand-name{font-weight:700;font-size:34px;color:var(--dark);letter-spacing:.5px}
.main-nav{position:absolute;top:44px;left:556px;display:flex;gap:30px;font-size:16px;color:#333}
.main-nav .drop::after{content:" ▾";font-size:11px}
.nav-tools{position:absolute;top:40px;left:1024px;display:flex;gap:14px;align-items:center}
.nav-tools .sep{width:2px;height:18px;background:var(--red)}

/* hero */
.hero{position:absolute;top:113px;left:0;width:1200px;height:577px;background:linear-gradient(120deg,#3d3b38 0%,#6b645a 45%,#8a8177 65%,#3f3b37 100%)}
.hero h1{position:absolute;top:198px;width:100%;text-align:center;color:#fff;font-weight:700;font-size:62px;line-height:72px}
.hero-arrow{position:absolute;top:265px;width:48px;height:48px;border-radius:50%;display:flex;align-items:center;justify-content:center}
.hero-arrow.prev{left:24px;background:#1a1a1a}
.hero-arrow.next{right:24px;background:var(--red)}

/* services strip */
.services{position:absolute;top:690px;left:0;width:1200px;height:217px;background:#fff}
.services-intro{position:absolute;left:0;top:0;width:333px;height:210px;background:var(--red);color:#fff;padding:28px 0 0 94px}
.services-intro h2{font-size:34px;font-weight:700;margin-bottom:10px}
.services-intro p{font-size:14.5px;line-height:23px;font-weight:500;width:220px}
.service-item{position:absolute;top:0;height:210px}
.service-item svg{position:absolute;top:38px;left:50%;transform:translateX(-50%)}
.service-item .service-label{position:absolute;top:166px;left:0;width:100%;text-align:center;font-size:16px;font-weight:600;white-space:nowrap}
.services-rule{position:absolute;top:210px;height:7px}

/* catalog */
.section-title{font-size:38px;font-weight:700;color:var(--red);text-align:center}
.lead{font-size:16px;line-height:27px;color:var(--muted);text-align:center}
.catalog-card{position:absolute;top:1145px;width:306px;height:347px;background:var(--card)}
.catalog-card .stripe{position:absolute;bottom:0;left:0;width:100%;height:9px;background:linear-gradient(90deg,var(--yellow) 0 33.3%,var(--green) 33.3% 66.6%,var(--red) 66.6%)}
.catalog-card svg{position:absolute;left:50%;top:50%;transform:translate(-50%,-55%)}
.catalog-label{position:absolute;top:1520px;width:306px;text-align:center;font-size:27px;font-weight:700;color:var(--red);letter-spacing:.5px}
.btn{position:absolute;background:var(--red);color:#fff;font-weight:600;font-size:18px;border-radius:30px;display:flex;align-items:center;justify-content:center}

/* welcome */
.welcome{position:absolute;top:1794px;left:0;width:1200px;height:443px;background:var(--light)}

/* gallery */
.gallery-filter{position:absolute;left:94px;top:2404px;width:220px}
.gallery-filter li{list-style:none;font-size:19px;color:#444;height:63px;padding-left:16px;line-height:47px;white-space:nowrap}
.gallery-filter li.active{background:var(--red);color:#fff;font-weight:600;width:125px;height:47px;margin-bottom:16px}
.gallery-grid{position:absolute;left:328px;top:2416px;width:872px;height:368px;display:grid;grid-template-columns:repeat(3,1fr);grid-template-rows:repeat(2,1fr)}
.gallery-grid div:nth-child(1){background:linear-gradient(135deg,#c9c2d8,#e9d7e0)}
.gallery-grid div:nth-child(2){background:linear-gradient(135deg,#d9dbd8,#9aa6a0)}
.gallery-grid div:nth-child(3){background:linear-gradient(135deg,#6f7a80,#c9c2b4)}
.gallery-grid div:nth-child(4){background:linear-gradient(135deg,#8d8a86,#e2dfda)}
.gallery-grid div:nth-child(5){background:linear-gradient(135deg,#d8d4cc,#9b8f7f)}
.gallery-grid div:nth-child(6){background:linear-gradient(135deg,#7d6f6a,#c9bcb4)}

/* delivery */
.delivery{position:absolute;top:2869px;left:0;width:1200px;height:297px;background:var(--light)}
.delivery-item{position:absolute;top:64px;width:220px;text-align:center}
.delivery-item .disc{width:108px;height:108px;border-radius:50%;margin:0 auto;display:flex;align-items:center;justify-content:center}
.delivery-item p{margin-top:20px;font-size:17.5px;line-height:27px;color:#333}

/* footer */
.site-footer{position:absolute;top:3166px;left:0;width:1200px;height:370px;background:var(--dark);color:#fff}
.footer-col{position:absolute;top:40px}
.footer-col h3{font-size:20px;font-weight:600;margin-bottom:26px}
.footer-col li{list-style:none;font-size:14.5px;line-height:32px;color:#ddd}
.footer-divider{position:absolute;top:92px;width:1px;height:180px;background:#4a4a4a}
.social{display:flex;gap:10px}
.social span{width:30px;height:30px;border:2px solid #fff;border-radius:50%}
.cards{position:absolute;top:193px;display:flex;gap:4px}
.cards span{width:32px;height:20px;border-radius:2px}
.footer-bottom{position:absolute;top:285px;left:94px;width:1012px;height:1px;background:#444}
.copyright{position:absolute;top:310px;width:100%;text-align:center;font-size:15px;color:#ddd}
</style>
</head>
<body>

<header class="site-header">
  <div class="brand"><span class="brand-mark"></span><span class="brand-name">VINDURGATA</span></div>
  <nav class="main-nav">
    <span>Home</span><span class="drop">Services</span><span>Submission of Works</span><span>About Us</span>
  </nav>
  <div class="nav-tools">
    <svg width="18" height="18" viewBox="0 0 18 18"><circle cx="7.5" cy="7.5" r="5.5" fill="none" stroke="#e8402f" stroke-width="2.4"/><line x1="11.5" y1="11.5" x2="16.5" y2="16.5" stroke="#e8402f" stroke-width="2.6"/></svg>
    <span class="sep"></span>
    <svg width="18" height="18" viewBox="0 0 18 18"><rect x="2" y="6" width="14" height="11" rx="1" fill="#e8402f"/><path d="M6 6V4a3 3 0 0 1 6 0v2" fill="none" stroke="#e8402f" stroke-width="2"/></svg>
  </div>
</header>

<section class="hero" role="img" aria-label="Printer operator inspecting fresh sheets in a print shop">
  <h1>Make A Professional<br>First Impression</h1>
  <div class="hero-arrow prev"><svg width="14" height="14" viewBox="0 0 14 14"><path d="M9 2 4 7l5 5" fill="none" stroke="#fff" stroke-width="2.4"/></svg></div>
  <div class="hero-arrow next"><svg width="14" height="14" viewBox="0 0 14 14"><path d="M5 2l5 5-5 5" fill="none" stroke="#fff" stroke-width="2.4"/></svg></div>
</section>

<section class="services">
  <div class="services-intro">
    <h2>Services</h2>
    <p>Online and in store, you can find printing services to help you get the job done</p>
  </div>
  <div class="service-item" style="left:333px;width:260px">
    <svg width="64" height="86" viewBox="0 0 64 86" fill="none" stroke="#e8402f" stroke-width="3"><path d="M6 10 52 2v74L6 84z"/><path d="M52 10h6v70H6"/><circle cx="29" cy="43" r="13"/><path d="M16 43h26M29 30c-6 8-6 18 0 26M29 30c6 8 6 18 0 26"/></svg>
    <span class="service-label" style="color:var(--red)">Tourist Brochure</span>
  </div>
  <div class="service-item" style="left:593px;width:162px">
    <svg width="84" height="84" viewBox="0 0 84 84" fill="none" stroke="#1e6b3c" stroke-width="3.5"><rect x="12" y="4" width="60" height="22"/><rect x="4" y="26" width="76" height="34" rx="3"/><circle cx="56" cy="40" r="8"/><rect x="16" y="60" width="52" height="20"/><path d="M24 68h36M24 74h36M12 36h20"/></svg>
    <span class="service-label" style="color:var(--green)">Digital Printing</span>
  </div>
  <div class="service-item" style="left:755px;width:218px">
    <svg width="84" height="74" viewBox="0 0 84 74" fill="none" stroke="#e8402f" stroke-width="3.5"><path d="M14 4h66v60a6 6 0 0 1-6 6H10a6 6 0 0 1-6-6V22h10"/><path d="M14 4v60"/><rect x="24" y="16" width="22" height="18" fill="#e8402f"/><path d="M52 18h20M52 28h20M24 44h48M24 54h48"/></svg>
    <span class="service-label" style="color:var(--red)">Reports</span>
  </div>
  <div class="service-item" style="left:973px;width:227px">
    <svg width="70" height="92" viewBox="0 0 70 92" fill="none" stroke="#222" stroke-width="3.5"><rect x="4" y="4" width="62" height="84" rx="3"/><path d="M14 4v84"/><path d="M40 26l12 6v14l-12 6-12-6V32zM28 32l12 6 12-6M40 38v14"/><path d="M24 72h34"/></svg>
    <span class="service-label" style="color:#222">Book Print</span>
  </div>
  <div class="services-rule" style="left:0;width:333px;background:#1a1a1a"></div>
  <div class="services-rule" style="left:333px;width:260px;background:var(--yellow)"></div>
  <div class="services-rule" style="left:593px;width:162px;background:var(--green)"></div>
  <div class="services-rule" style="left:755px;width:218px;background:var(--red)"></div>
  <div class="services-rule" style="left:973px;width:227px;background:#1a1a1a"></div>
</section>

<h2 class="section-title abs" style="top:978px;left:0;width:1200px">Catalog</h2>
<p class="lead abs" style="top:1042px;left:270px;width:660px">Lorem ipsum dolor sit amet, consectetur adipiscing elit, sed do eiusmod tempor incididunt ut labore et dolore magna aliqua.</p>

<div class="catalog-card" style="left:111px">
  <svg width="160" height="124" viewBox="0 0 160 124" fill="none" stroke="#f6c817" stroke-width="5"><rect x="4" y="4" width="152" height="116" rx="8"/><circle cx="42" cy="50" r="14"/><path d="M20 96c0-18 10-28 22-28s22 10 22 28z"/><path d="M80 44h58M80 62h58M80 80h40"/></svg>
  <div class="stripe"></div>
</div>
<div class="catalog-card" style="left:445px">
  <svg width="112" height="160" viewBox="0 0 112 160" fill="none" stroke="#1e6b3c" stroke-width="6"><path d="M4 16 38 4v144L4 156z"/><path d="M38 4l36 12v140l-36-8z"/><path d="M74 16l34-12v144l-34 8z"/><path d="M14 36h14v40H14M50 40v60M84 40h14v70"/></svg>
  <div class="stripe"></div>
</div>
<div class="catalog-card" style="left:782px">
  <svg width="170" height="160" viewBox="0 0 170 160" fill="none" stroke="#e8402f" stroke-width="6"><path d="M10 20a10 10 0 0 1 10-10h52v110H20a10 10 0 0 0-10 10V20z"/><path d="M10 130a10 10 0 0 0 10 10h120v-16"/><path d="M24 120h118V100"/><circle cx="118" cy="52" r="38"/><path d="M118 44v28M118 32v2"/><path d="M26 32h10M26 48h10M26 64h10M26 80h10"/></svg>
  <div class="stripe"></div>
</div>
<div class="catalog-label" style="left:111px">Business Cards</div>
<div class="catalog-label" style="left:445px">Pamphlets</div>
<div class="catalog-label" style="left:782px">Text Books</div>
<div class="btn" style="left:507px;top:1631px;width:190px;height:61px">Show More</div>

<section class="welcome">
  <h2 class="section-title abs" style="top:58px;left:0;width:1200px">Welcome to University</h2>
  <p class="lead abs" style="top:130px;left:150px;width:900px;font-size:16px;line-height:30px">University education is a company located in the campus, which has specialized in the service of school staff, as well as providing general public printing.Higher education publishes seminars and first-class textbooks for courses, prints theses for lesson, as well as working on an unprecedented number of smaller pieces for students, teachers and organizations. These include brochures, reports, questionnaires, business cards, books, OCR scanning and more.</p>
  <div class="btn" style="left:504px;top:311px;width:192px;height:59px">Read More</div>
</section>

<h2 class="abs" style="top:2300px;left:94px;font-size:38px;font-weight:700;color:var(--red)">Gallery</h2>
<ul class="gallery-filter">
  <li class="active">All</li><li>Business Cards</li><li>Pamphlets</li><li>Book Printing</li><li>Poster</li><li>Text Books</li>
</ul>
<div class="gallery-grid">
  <div role="img" aria-label="Printed business cards in pastel tones"></div>
  <div role="img" aria-label="Open printed brochure"></div>
  <div role="img" aria-label="Roll-up banner beside a glass building"></div>
  <div role="img" aria-label="Stack of printed magazines"></div>
  <div role="img" aria-label="Fanned printed booklets"></div>
  <div role="img" aria-label="Pile of glossy magazines"></div>
</div>

<section class="delivery">
  <div class="delivery-item" style="left:173px">
    <div class="disc" style="background:var(--yellow)"><svg width="56" height="40" viewBox="0 0 56 40" fill="none" stroke="#fff" stroke-width="3.5"><path d="M14 6h26v24H14M40 14h8l6 8v8H40"/><circle cx="20" cy="32" r="4"/><circle cx="46" cy="32" r="4"/><path d="M2 14h10M4 22h10"/></svg></div>
    <p>Shipping by Courier</p>
  </div>
  <div class="delivery-item" style="left:395px">
    <div class="disc" style="background:var(--green)"><svg width="52" height="48" viewBox="0 0 52 48" fill="none" stroke="#fff" stroke-width="3.5"><path d="M4 18 26 4l22 14v26H4z"/><path d="M4 18l22 16 22-16"/><path d="M14 14h24v12"/></svg></div>
    <p>Registered Mail<br>Delivery</p>
  </div>
  <div class="delivery-item" style="left:616px">
    <div class="disc" style="background:var(--red)"><svg width="54" height="50" viewBox="0 0 54 50" fill="none" stroke="#fff" stroke-width="3.5"><path d="M6 4h42l4 14H2z"/><path d="M6 18v28h42V18"/><rect x="14" y="28" width="12" height="18"/><rect x="32" y="28" width="10" height="8"/></svg></div>
    <p>Delivery<br>To Service Centers</p>
  </div>
  <div class="delivery-item" style="left:840px">
    <div class="disc" style="background:#141414"><svg width="52" height="54" viewBox="0 0 52 54" fill="none" stroke="#fff" stroke-width="3.5"><path d="M4 22l14-4 16 4 14-4v32l-14 4-16-4-14 4z"/><path d="M18 18v32M34 22v32"/><path d="M26 4a8 8 0 0 1 8 8c0 6-8 14-8 14s-8-8-8-14a8 8 0 0 1 8-8z" fill="#141414"/></svg></div>
    <p>Pickup</p>
  </div>
</section>

<footer class="site-footer">
  <div class="footer-col" style="left:94px"><h3>Useful Links</h3><ul><li>Home</li><li>Services</li><li>Submission of Works</li><li>About Us</li></ul></div>
  <div class="footer-divider" style="left:317px"></div>
  <div class="footer-col" style="left:408px"><h3>Other Links</h3><ul><li>Privacy Policy</li><li>Customer</li><li>Satisfaction</li><li>Secure Shopping</li><li>Digital Printing</li></ul></div>
  <div class="footer-divider" style="left:596px"></div>
  <div class="footer-col" style="left:658px"><h3>Support</h3><ul><li>Services</li><li>FAQ</li><li>Terms and concepts</li><li>Privacy Policy</li></ul></div>
  <div class="footer-col" style="left:931px"><h3>Stay Connected</h3><div class="social"><span></span><span></span><span></span></div></div>
  <div class="cards" style="left:931px">
    <span style="background:#3b6fc4"></span><span style="background:#e0523c"></span><span style="background:#e8a23a"></span><span style="background:#4aa3d8"></span><span style="background:#2d5aa6"></span>
  </div>
  <div class="footer-bottom"></div>
  <p class="copyright">© 2018 Copyrights | All Rights Reserved</p>
</footer>

</body>
</html>
```